Structural Engineering Business Card

Brookvane Drafting does residential house plans for clients in Central Florida. Would like simple but elegant business card that is appropriate for a house plan engineering company. Prefer black business card with black/white them but open to other shades of blue. I uploaded a sample card that I came across that looked good but please come up with your own creative designs.

Contact Information for Business Card

Name, Title, Phone, Email, Address, website

```html
<!DOCTYPE html>
<html lang="en">
<head>
<meta charset="utf-8">
<title>Brookvane Drafting – Business Card</title>
<link href="https://fonts.googleapis.com/css2?family=Montserrat:wght@400;500;800&display=swap" rel="stylesheet">
<style>
  :root {
    --backdrop: #d9d4cc;
    --card-black: #1c1a19;
    --frost-light: #d8d2c8;
    --frost-mid: #b9b1a6;
    --text-name: #ece4d6;
    --text-body: #c9bfae;
    --brand-white: #f4f1ec;
  }
  html, body {
    margin: 0;
    width: 1200px;
    height: 887px;
    overflow: hidden;
    background: var(--backdrop);
  }
  .card {
    position: absolute;
    left: 100px;
    top: 163px;
    width: 1000px;
    height: 560px;
    border-radius: 26px;
    background: var(--card-black);
    overflow: hidden;
    font-family: "Montserrat", sans-serif;
  }
  .map-area {
    position: absolute;
    left: 440px;
    top: 0;
    width: 260px;
    height: 560px;
    background: linear-gradient(160deg, var(--frost-light), var(--frost-mid));
  }
  .contact-block {
    position: absolute;
    left: 60px;
    top: 250px;
    color: var(--text-body);
  }
  .person-name {
    margin: 0;
    font-size: 29px;
    font-weight: 500;
    letter-spacing: 1.5px;
    color: var(--text-name);
  }
  .person-title {
    margin: 4px 0 24px;
    font-size: 21px;
    font-weight: 400;
    letter-spacing: 1px;
  }
  .address {
    margin: 0 0 22px;
    font-size: 23px;
    line-height: 33px;
    font-style: normal;
  }
  .contact-list {
    list-style: none;
    margin: 0;
    padding: 0;
    font-size: 22px;
    line-height: 32px;
  }
  .contact-list li {
    display: flex;
    align-items: center;
    gap: 8px;
  }
  .contact-icon {
    width: 16px;
    height: 16px;
    fill: none;
    stroke: var(--text-body);
    stroke-width: 1.8;
  }
  .brand-name {
    position: absolute;
    left: 850px;
    top: 280px;
    transform: translate(-50%, -50%) rotate(-90deg);
    white-space: nowrap;
    font-size: 34px;
    font-weight: 800;
    letter-spacing: 1px;
    color: var(--brand-white);
    text-transform: uppercase;
  }
</style>
</head>
<body>
  <div class="card">
    <div class="map-area" role="img" aria-label="Frosted clear state map silhouette"></div>

    <div class="contact-block">
      <h1 class="person-name">DANIEL HARTWELL</h1>
      <p class="person-title">DIRECTOR</p>
      <address class="address">1480 Willow Crest Lane<br>Orlando, FL 32803</address>
      <ul class="contact-list">
        <li>
          <svg class="contact-icon" viewBox="0 0 16 16"><path d="M3 1.5 L6 1.5 L7 5 L5 6.5 Q6.5 9.5 9.5 11 L11 9 L14.5 10 L14.5 13 Q14 14.5 12.5 14.5 Q5 14 1.5 3.5 Q1.5 2 3 1.5 Z"/></svg>
          407.555.0182
        </li>
        <li>
          <svg class="contact-icon" viewBox="0 0 16 16"><rect x="1.5" y="3.5" width="13" height="9"/><path d="M1.5 3.5 L8 9 L14.5 3.5"/></svg>
          info@brookvane.com
        </li>
        <li>
          <svg class="contact-icon" viewBox="0 0 16 16"><circle cx="8" cy="8" r="6.5"/><ellipse cx="8" cy="8" rx="3" ry="6.5"/><path d="M1.5 8 H14.5"/></svg>
          www.brookvane.com
        </li>
      </ul>
    </div>

    <div class="brand-name">Brookvane Drafting</div>
  </div>
</body>
</html>
```